Dov's Personal Training -> also needs a logo

Services Frankston, Mornington, and Somerville

Specializes in in-home personal training

VaultPace style workouts

Not really preferential colors but needs to look modern and not stock photo

Industry/Entity Type

Training

Requirements
Must have
• 30% off first time customers on a package of 10

```html
<!DOCTYPE html>
<html lang="en">
<head>
<meta charset="utf-8">
<title>Dov's Personal Training</title>
<link href="https://fonts.googleapis.com/css2?family=Archivo:wght@700;800;900&family=Roboto+Condensed:wght@300;400;700&display=swap" rel="stylesheet">
<style>
  :root {
    --ink: #ffffff;
    --night: #050508;
    --lime: #3fd61c;
    --leaf: #1f8a14;
    --violet: #a21fd0;
    --indigo: #4a2bd6;
    --sky: #2a6fe0;
    --brand: #d69ae8;
    --panel: #1c231c;
  }
  * { margin: 0; padding: 0; box-sizing: border-box; }
  html, body { width: 1200px; height: 900px; overflow: hidden; background: var(--night); }
  .flyer {
    position: relative;
    width: 1200px;
    height: 900px;
    overflow: hidden;
    color: var(--ink);
    font-family: "Roboto Condensed", "Arial Narrow", sans-serif;
  }
  .light-streaks {
    position: absolute;
    inset: 0;
    background:
      radial-gradient(ellipse 520px 420px at 120px 760px, rgba(63,214,28,0.85), transparent 70%),
      radial-gradient(ellipse 420px 520px at 380px 620px, rgba(40,160,20,0.55), transparent 70%),
      radial-gradient(ellipse 460px 420px at 880px 140px, rgba(162,31,208,0.85), transparent 70%),
      radial-gradient(ellipse 380px 520px at 1120px 300px, rgba(74,43,214,0.8), transparent 70%),
      radial-gradient(ellipse 360px 420px at 1150px 780px, rgba(42,111,224,0.7), transparent 70%),
      radial-gradient(ellipse 360px 300px at 700px 650px, rgba(70,120,40,0.35), transparent 70%),
      linear-gradient(160deg, #070709 0%, #0b0d0a 40%, #0a0710 100%);
  }
  .brand {
    position: absolute;
    left: 78px;
    top: 60px;
    width: 430px;
    display: flex;
    flex-direction: column;
    align-items: flex-end;
    font-family: "Archivo", Arial, sans-serif;
    font-weight: 800;
    color: var(--brand);
  }
  .brand-name { font-size: 150px; line-height: 1; letter-spacing: 2px; align-self: flex-start; }
  .brand-tag { font-size: 42px; line-height: 1.1; margin-top: 14px; text-align: right; }
  .specialties {
    position: absolute;
    left: 577px;
    top: 142px;
    text-transform: uppercase;
    font-size: 38px;
    line-height: 1.05;
  }
  .specialties-title { font-weight: 700; }
  .specialties-item { font-weight: 300; letter-spacing: 0.5px; }
  .service-area {
    position: absolute;
    left: 40px;
    top: 672px;
    width: 278px;
    height: 228px;
    background: var(--panel);
    padding: 28px 0 0 28px;
    text-transform: uppercase;
    font-size: 36px;
    line-height: 1.03;
  }
  .service-area-title { font-weight: 700; }
  .service-area-town { font-weight: 300; }
  .offer {
    position: absolute;
    right: 58px;
    top: 442px;
    text-align: right;
    font-family: "Archivo", Arial, sans-serif;
  }
  .offer-amount {
    display: block;
    font-weight: 900;
    font-size: 186px;
    line-height: 0.86;
    letter-spacing: -4px;
  }
  .offer-terms {
    display: block;
    font-weight: 700;
    font-size: 37px;
    line-height: 1.2;
    margin-top: 10px;
    letter-spacing: 0.5px;
  }
</style>
</head>
<body>
<main class="flyer">
  <div class="light-streaks" role="img" aria-label="Abstract diagonal light streaks in green, purple and blue on black"></div>

  <div class="brand">
    <span class="brand-name">DOV'S</span>
    <span class="brand-tag">Personal<br>Training</span>
  </div>

  <section class="specialties">
    <p class="specialties-title">Specializes in:</p>
    <p class="specialties-item">In-home personal training</p>
    <p class="specialties-item">VaultPace style workouts</p>
  </section>

  <section class="service-area">
    <p class="service-area-title">Services:</p>
    <p class="service-area-town">Frankston</p>
    <p class="service-area-town">Mornington</p>
    <p class="service-area-town">Somerville</p>
  </section>

  <section class="offer">
    <span class="offer-amount">30%<br>OFF</span>
    <span class="offer-terms">first time customers<br>on a package of 10</span>
  </section>
</main>
</body>
</html>
```